Brightway Haul & Upkeep Services, are a company that offers a 'one stop shop' pre-move clean up a

I have already selected a logo which I would like on the front of the business cards along with phone numbers, web address and email which are:
0487650392
www.brightwayhaul.com.au
brightwayhaulandupkeep@mailbox.example

On the back of the card I would like to list some of the types of service we offer (clean - move - repairs/maintenance) which are:
CLEAN - windows, gutters, solar panels, driveways/paths, carpets.
MOVE - Small/medium size house/office moves, large item pick-up & delivery, yard clean-up and removal.
General maintenance and repairs.

I would like the blue logo on a gray background.

Thanks

```html
<!DOCTYPE html>
<html lang="en">
<head>
<meta charset="utf-8">
<title>Brightway Haul &amp; Upkeep Services – Business Cards</title>
<link rel="stylesheet" href="https://fonts.googleapis.com/css2?family=Jost:wght@400;500;700&display=swap">
<style>
  :root {
    --backdrop: #e9e7e4;
    --card-light: #e4e5e6;
    --card-mid: #c9cacc;
    --brand-blue: #2a6fc0;
    --band-black: #1f1d1e;
    --ink-dark: #231f20;
    --white: #ffffff;
  }
  * { box-sizing: border-box; margin: 0; padding: 0; }
  html, body {
    width: 1200px; height: 682px; overflow: hidden;
    background: var(--backdrop);
    font-family: "Jost", sans-serif;
  }
  .sheet {
    width: 1200px; height: 682px;
    display: flex; align-items: center; justify-content: center; gap: 40px;
  }
  .card {
    position: relative;
    width: 540px; height: 330px;
    border-radius: 18px;
    overflow: hidden;
    background: linear-gradient(160deg, var(--card-light) 0%, var(--card-mid) 100%);
    box-shadow: 0 8px 22px rgba(0,0,0,0.18);
  }
  .brand-name {
    color: var(--brand-blue);
    font-weight: 700;
    text-transform: uppercase;
    text-align: center;
    line-height: 1.02;
    letter-spacing: 0.5px;
  }
  .brand-name .line-main { display: block; font-size: 44px; }
  .brand-name .line-sub { display: block; font-size: 23px; }

  /* Front */
  .card-front .brand-name { position: absolute; left: 0; right: 0; top: 58px; }
  .contact-band {
    position: absolute; left: 0; right: 0; top: 206px; height: 78px;
    background: var(--band-black);
    display: flex; align-items: center; justify-content: center; gap: 18px;
    color: var(--white); font-size: 15px;
  }
  .contact-item { display: flex; align-items: center; gap: 7px; }
  .contact-item svg { width: 14px; height: 14px; fill: var(--white); }
  .divider { width: 2px; height: 26px; background: var(--white); transform: skewX(-12deg); }
  .web-band {
    position: absolute; left: 0; right: 0; bottom: 0; height: 46px;
    background: var(--brand-blue);
    display: flex; align-items: center; justify-content: center;
    color: var(--white); font-size: 15px; letter-spacing: 4px;
  }

  /* Back */
  .card-back .brand-name { position: absolute; left: 0; right: 0; top: 44px; }
  .services {
    position: absolute; left: 0; right: 0; top: 170px;
    text-align: center;
  }
  .services-title {
    color: var(--brand-blue);
    font-size: 24px; font-weight: 500;
    letter-spacing: 6px;
    margin-bottom: 12px;
  }
  .services-list { list-style: none; color: var(--ink-dark); font-size: 18px; font-weight: 500; line-height: 1.55; }
  .bullet { color: var(--brand-blue); }
</style>
</head>
<body>
<main class="sheet">

  <section class="card card-front" aria-label="Business card front">
    <h1 class="brand-name">
      <span class="line-main">Brightway Haul</span>
      <span class="line-sub">&amp; Upkeep Services</span>
    </h1>
    <div class="contact-band">
      <span class="contact-item">
        <svg viewBox="0 0 24 24" aria-hidden="true"><path d="M6.6 10.8a15.1 15.1 0 0 0 6.6 6.6l2.2-2.2c.3-.3.7-.4 1-.2 1.1.4 2.3.6 3.6.6.6 0 1 .4 1 1V20c0 .6-.4 1-1 1A17 17 0 0 1 3 4c0-.6.4-1 1-1h3.5c.6 0 1 .4 1 1 0 1.3.2 2.5.6 3.6.1.3 0 .7-.2 1L6.6 10.8z"/></svg>
        0487650392
      </span>
      <span class="divider" aria-hidden="true"></span>
      <span class="contact-item">
        <svg viewBox="0 0 24 24" aria-hidden="true"><path d="M2 5h20v14H2z M3.5 6.5 12 13l8.5-6.5" fill="none" stroke="#fff" stroke-width="2"/></svg>
        brightwayhaulandupkeep@mailbox.example
      </span>
    </div>
    <div class="web-band">www.brightwayhaul.com.au</div>
  </section>

  <section class="card card-back" aria-label="Business card back">
    <h2 class="brand-name">
      <span class="line-main">Brightway Haul</span>
      <span class="line-sub">&amp; Upkeep Services</span>
    </h2>
    <div class="services">
      <p class="services-title">Services we offer</p>
      <ul class="services-list">
        <li><span class="bullet">•</span> CLEAN &nbsp;<span class="bullet">•</span> MOVE</li>
        <li><span class="bullet">•</span> GENERAL MAINTENANCE AND REPAIRS.</li>
      </ul>
    </div>
  </section>

</main>
</body>
</html>
```